Stationery Design Project for Marketing Consultancy

I have started a new consultancy business and require the following elements to be designed using existing logo:
• Business card
• Letterhead
• Envelope (DL, C4, C5)
• Microsoft word template for report writing
• A4 Presentation Folder
• Powerpoint template
COPY FOR FRONT AND BACK OF BUSINESS CARD
logo
'Measurable Marketing. Epic Results' slogan (but no need to use existing lockup with logo)
name, B Bus. Mktg, Grad Dip Digital Mktg, CPM (post nominal abbreviations in smaller font)
mobile: 04XX-XXX-XXX (I will give details to the winner to add)
website: www.tolvarin.com.au
email: info@tolvarin.com.au
COPY FOR LETTERHEAD
Logo
Company Name
Please, submit your designs that include business card, letterhead and envelope. Once selected the winner will be asked to complete the project by creating the rest of the artwork.
FINAL FILES
Print ready files to be supplied as well as Indesign files so that minor amends can be made if necessary in future.
• Layered vectors in EPS & PDF
• Screen quality JPEG & PNGs
ABOUT THE BUSINESS: TOLVARIN
I work with clients to understand their business challenges, developing and executing measurable marketing strategies tied to key business metrics. Services include:
Services include:
• Business planning and business development
• Marketing and brand strategy
• Insight-driven integrated campaigns
• Loyalty programs and retention marketing
• Marketing automation
• Direct marketing (traditional and digital)
• Content strategy and development
Hi everyone,
Target Market(s)
Corporate decision makers (heads of marketing, general managers etc) and small to medium sized business owners. Predominately male aged 35+
Industry/Entity Type
Marketing
Requirements
Must have
- BRAND PERSONALITY
The successful design will communicate brand personality. I am a professional, results-driven entrepreneur, but want to show off my creative flair.
MEMORABILITY
Looking for a unique and eye-catching design. Am considering special printing effects (die cuts, letterpress, interactive elements, embossing, foiling etc) or a striking minimalist approach.
Nice to have
- I have a mission that could be incorporated on reverse if room -
Turning insights into actions & passion into profit.
Should not have
- Use of pink or green.

```html
<!DOCTYPE html>
<html lang="en">
<head>
<meta charset="utf-8">
<title>Tolvarin Letterhead</title>
<link rel="stylesheet" href="https://fonts.googleapis.com/css2?family=Mulish:wght@300;400;700&display=swap">
<style>
  :root {
    --backdrop: #e4e4e4;
    --paper: #f4f4f4;
    --ink: #85868e;
    --ink-soft: #a4a5ac;
    --ghost: #e3e3e6;
  }
  * { margin: 0; padding: 0; box-sizing: border-box; }
  html, body {
    width: 1200px;
    height: 968px;
    overflow: hidden;
    background: var(--backdrop);
    font-family: "Mulish", Arial, sans-serif;
  }
  .canvas {
    position: relative;
    width: 1200px;
    height: 968px;
    display: flex;
    align-items: center;
    justify-content: center;
  }
  .letterhead {
    position: relative;
    width: 630px;
    height: 891px;
    background: var(--paper);
    box-shadow: 0 2px 10px rgba(0,0,0,0.12);
    overflow: hidden;
  }
  .brand {
    position: absolute;
    top: 52px;
    left: 0;
    right: 0;
    display: flex;
    flex-direction: column;
    align-items: center;
    gap: 8px;
  }
  .brand-dot {
    width: 30px;
    height: 30px;
    border-radius: 50%;
    background: var(--ink);
  }
  .brand-name {
    font-weight: 700;
    font-size: 20px;
    letter-spacing: 3px;
    color: var(--ink);
  }
  .corner-mark {
    position: absolute;
    border-radius: 50%;
    background: var(--ghost);
  }
  .corner-mark--left { width: 70px; height: 70px; left: -22px; bottom: 190px; }
  .corner-mark--right { width: 150px; height: 150px; right: -40px; bottom: -40px; }
  .footer {
    position: absolute;
    left: 58px;
    bottom: 60px;
    width: 330px;
  }
  .slogan {
    font-weight: 400;
    font-size: 15.5px;
    letter-spacing: 0.3px;
    color: var(--ink);
    white-space: nowrap;
  }
  .slogan strong { font-weight: 700; }
  .footer-rule {
    height: 1px;
    background: var(--ink-soft);
    margin: 7px 0 8px;
  }
  .contacts {
    font-weight: 300;
    font-size: 9px;
    color: var(--ink);
    white-space: nowrap;
  }
  .contacts .sep { margin: 0 5px; }
  .contacts .web strong { font-weight: 700; }
</style>
</head>
<body>
  <main class="canvas">
    <article class="letterhead">
      <header class="brand">
        <span class="brand-dot"></span>
        <span class="brand-name">TOLVARIN</span>
      </header>

      <span class="corner-mark corner-mark--left"></span>
      <span class="corner-mark corner-mark--right"></span>

      <footer class="footer">
        <p class="slogan">CLEAR STRATEGY. <strong>BOLDER OUTCOMES.</strong></p>
        <div class="footer-rule"></div>
        <p class="contacts">
          <span>Mobile: +0491-570-156</span><span class="sep">·</span>
          <span>info@tolvarin.com.au</span><span class="sep">·</span>
          <span class="web">www.<strong>tolvarin</strong>.com.au</span>
        </p>
      </footer>
    </article>
  </main>
</body>
</html>
```